KORV PTY LTD - Business Cards

Design a modern business card - using the attached Designs.
Same design as on the front, apart from the names/numbers/emails to be different.
We want the cards to be very glossy to stand out, do I think the simple black/white/metallic will be effective.
Both lots of details below:

Tom Wrenshaw
Director
tom_korv@nulvane.com
0438 274 093

Lewis Corbyn
Director
lewis_korv@nulvane.com
0419 385 642

Industry/Entity Type

Business

```html
<!DOCTYPE html>
<html lang="en">
<head>
<meta charset="utf-8">
<title>KORV PTY LTD – Business Card</title>
<link rel="stylesheet" href="https://fonts.googleapis.com/css2?family=Exo+2:wght@300;400;600&display=swap">
<style>
  :root {
    --stage: #e9e7e3;
    --card-white: #f7f7f7;
    --card-white-edge: #e6e6e6;
    --panel: #3a3f44;
    --panel-band: #55595e;
    --rule: #8a8e93;
    --ink-light: #f2f2f2;
    --ink-soft: #cfd2d5;
    --ink-dark: #2f3337;
    --silver-a: #9a9a9a;
    --silver-b: #d4d4d4;
  }
  * { box-sizing: border-box; margin: 0; padding: 0; }
  html, body { width: 1200px; height: 672px; overflow: hidden; }
  body {
    background: var(--stage);
    font-family: "Exo 2", sans-serif;
    position: relative;
  }
  .card {
    position: absolute;
    top: 38px;
    width: 340px;
    height: 596px;
    border-radius: 6px;
    box-shadow: 0 10px 28px rgba(0,0,0,.22);
    overflow: hidden;
  }
  .card--front {
    left: 230px;
    background: linear-gradient(160deg, var(--card-white) 0%, var(--card-white-edge) 100%);
  }
  .card--back {
    left: 630px;
    background: linear-gradient(160deg, #454a50 0%, var(--panel) 100%);
  }
  .silver-strip {
    position: absolute;
    top: 0; left: 18px; right: 18px;
    height: 14px;
    border-radius: 0 0 7px 7px;
    background: linear-gradient(90deg, var(--silver-a), var(--silver-b) 50%, var(--silver-a));
  }
  .brand {
    position: absolute;
    top: 90px; left: 0; right: 0;
    display: flex; align-items: center; justify-content: center; gap: 10px;
  }
  .brand__dot {
    width: 22px; height: 22px; border-radius: 50%;
    background: var(--ink-dark);
  }
  .brand__name {
    font-weight: 600; font-size: 22px; letter-spacing: 2px;
    color: var(--ink-dark);
  }
  .panel {
    position: absolute;
    top: 198px; left: 14px; right: 14px; bottom: 16px;
    background: var(--panel);
    border-radius: 18px 18px 0 0;
    color: var(--ink-light);
  }
  .panel__header {
    height: 66px;
    background: var(--panel-band);
    border-radius: 18px 18px 0 0;
    border-bottom: 1px solid var(--rule);
    text-align: center;
    padding-top: 12px;
  }
  .person__name { font-weight: 400; font-size: 20px; letter-spacing: 1.5px; text-transform: uppercase; }
  .person__role { font-weight: 300; font-size: 13px; letter-spacing: 2px; text-transform: uppercase; color: var(--ink-soft); margin-top: 2px; }
  .contacts { list-style: none; padding: 26px 0 0 40px; }
  .contacts li {
    display: flex; align-items: center; gap: 12px;
    font-weight: 300; font-size: 15px; letter-spacing: 1px;
    height: 30px;
  }
  .contacts svg { width: 20px; height: 20px; flex: none; }
  .address {
    display: flex; gap: 12px; padding: 34px 0 0 40px;
    font-weight: 300; font-size: 15px; letter-spacing: .5px; line-height: 1.35;
  }
  .address svg { width: 20px; height: 20px; flex: none; margin-top: 1px; }
  .icon-ring { fill: none; stroke: var(--ink-light); stroke-width: 1.4; }
  .icon-mark { fill: var(--ink-light); }
  .icon-line { fill: none; stroke: var(--ink-light); stroke-width: 1.4; }
</style>
</head>
<body>
  <section class="card card--front" aria-label="Business card front">
    <div class="silver-strip"></div>
    <div class="brand">
      <span class="brand__dot"></span>
      <span class="brand__name">KORV PTY LTD</span>
    </div>
    <div class="panel">
      <header class="panel__header">
        <p class="person__name">Tom Wrenshaw</p>
        <p class="person__role">Director</p>
      </header>
      <ul class="contacts">
        <li>
          <svg viewBox="0 0 20 20"><circle class="icon-ring" cx="10" cy="10" r="9"/><path class="icon-mark" d="M7 5.5h2l.6 2.4-1.2.8a6 6 0 0 0 2.9 2.9l.8-1.2 2.4.6v2c0 .6-.5 1-1 1A8 8 0 0 1 6 6.5c0-.6.4-1 1-1z"/></svg>
          <span>0438 274 093</span>
        </li>
        <li>
          <svg viewBox="0 0 20 20"><circle class="icon-ring" cx="10" cy="10" r="9"/><rect class="icon-line" x="7" y="5" width="6" height="10" rx="1"/><circle class="icon-mark" cx="10" cy="13" r=".8"/></svg>
          <span>0438 274 093</span>
        </li>
        <li>
          <svg viewBox="0 0 20 20"><circle class="icon-ring" cx="10" cy="10" r="9"/><rect class="icon-line" x="6" y="8" width="8" height="5" rx="1"/><rect class="icon-line" x="7.5" y="5.5" width="5" height="2.5"/></svg>
          <span>0438 274 093</span>
        </li>
        <li>
          <svg viewBox="0 0 20 20"><circle class="icon-ring" cx="10" cy="10" r="9"/><circle class="icon-line" cx="10" cy="10" r="2.2"/><path class="icon-line" d="M12.2 8v3c0 1.4 2 1.4 2 0v-1a4.2 4.2 0 1 0-1.6 3.3"/></svg>
          <span>tom_korv@nulvane.com</span>
        </li>
        <li>
          <svg viewBox="0 0 20 20"></svg>
          <span>www.nulvane.com</span>
        </li>
      </ul>
      <div class="address">
        <svg viewBox="0 0 20 20"><circle class="icon-ring" cx="10" cy="10" r="9"/><path class="icon-mark" d="M10 4.5a3.5 3.5 0 0 0-3.5 3.5c0 2.6 3.5 7 3.5 7s3.5-4.4 3.5-7A3.5 3.5 0 0 0 10 4.5zm0 5a1.4 1.4 0 1 1 0-2.8 1.4 1.4 0 0 1 0 2.8z"/></svg>
        <p>27 Harlow Bend Road<br>4th Floor Suite B</p>
      </div>
    </div>
  </section>

  <section class="card card--back" aria-label="Business card back"></section>
</body>
</html>
```